Coastline Premier Retreats Business Card Design

Design a business card for Coastline Premier Retreats. Look at the website for colors and reference. Card should have logo, name, title, office number, mobile number, email, URL and a tagline like, "Luxury Hotel & Resort Email Marketing" (This might change).

https://www.coastlinepremierretreats.example

The rest I will leave up to your imagination.

Contact Information for Business Card

Logo, name, title, office number, mobile number, email, URL and a tagline like, "Luxury Hotel & Resort Email Marketing" (This might change).

```html
<!DOCTYPE html>
<html lang="en">
<head>
<meta charset="utf-8">
<title>Coastline Premier Retreats – Business Card</title>
<link href="https://fonts.googleapis.com/css2?family=Montserrat:wght@300;400;600;700;800&display=swap" rel="stylesheet">
<style>
  :root {
    --page-bg: #d9d9d9;
    --card-bg: #1b1b1b;
    --accent: #f07213;
    --ink-light: #f4f4f4;
    --mark-grey: #4a4a4a;
  }
  * { box-sizing: border-box; margin: 0; padding: 0; }
  html, body { width: 1200px; height: 1200px; overflow: hidden; }
  body {
    background: var(--page-bg);
    font-family: "Montserrat", Arial, sans-serif;
    position: relative;
  }
  .card {
    position: absolute;
    top: 215px;
    width: 440px;
    height: 770px;
    background: var(--card-bg);
    overflow: hidden;
  }
  .card--front { left: 130px; }
  .card--back { left: 630px; }

  /* Front */
  .brand {
    position: absolute;
    top: 92px;
    left: 0;
    width: 100%;
    display: flex;
    justify-content: center;
    align-items: center;
    gap: 14px;
  }
  .brand__square {
    width: 18px;
    height: 18px;
    background: var(--accent);
    flex: none;
  }
  .brand__name {
    color: var(--ink-light);
    font-weight: 700;
    font-size: 21px;
    letter-spacing: 1.5px;
    text-transform: uppercase;
    line-height: 1.25;
  }
  .name-bar {
    position: absolute;
    left: 0;
    top: 312px;
    width: 22px;
    height: 56px;
    background: var(--accent);
  }
  .person { position: absolute; left: 62px; top: 312px; }
  .person__name {
    color: var(--accent);
    font-weight: 800;
    font-size: 34px;
    letter-spacing: 1.5px;
    text-transform: uppercase;
    line-height: 1;
  }
  .person__title {
    color: var(--ink-light);
    font-weight: 400;
    font-size: 19px;
    margin-top: 6px;
  }
  .address {
    position: absolute;
    left: 62px;
    top: 440px;
    color: var(--ink-light);
    font-weight: 400;
    font-size: 18px;
    line-height: 1.45;
  }
  .contacts {
    position: absolute;
    left: 36px;
    top: 560px;
    list-style: none;
    color: var(--ink-light);
    font-size: 16px;
    font-weight: 400;
  }
  .contacts__item {
    display: flex;
    align-items: center;
    gap: 10px;
    height: 32px;
  }
  .contacts__icon { width: 16px; height: 16px; flex: none; }
  .contacts__domain { color: var(--accent); }

  /* Back */
  .back-mark {
    position: absolute;
    left: 170px;
    top: 385px;
    width: 600px;
    transform: translate(-50%, -50%) rotate(-90deg);
    text-align: center;
    color: var(--mark-grey);
    font-weight: 800;
    font-size: 46px;
    letter-spacing: 3px;
    text-transform: uppercase;
    line-height: 1.15;
  }
  .tagline {
    position: absolute;
    left: 352px;
    top: 385px;
    width: 600px;
    transform: translate(-50%, -50%) rotate(-90deg);
    text-align: center;
    color: var(--accent);
    font-weight: 400;
    font-size: 20px;
    letter-spacing: 0.3px;
    white-space: nowrap;
  }
</style>
</head>
<body>

<section class="card card--front" aria-label="Business card front">
  <div class="brand">
    <span class="brand__square"></span>
    <span class="brand__name">Coastline Premier<br>Retreats</span>
  </div>

  <div class="name-bar"></div>
  <div class="person">
    <h1 class="person__name">Daniel Reyes</h1>
    <p class="person__title">CEO/Founder</p>
  </div>

  <p class="address">Po Box, 48 Harbor Lane<br>Bayview, CA 90210</p>

  <ul class="contacts">
    <li class="contacts__item">
      <svg class="contacts__icon" viewBox="0 0 16 16" aria-hidden="true">
        <rect x="4" y="1" width="8" height="14" rx="1.5" fill="none" stroke="#f07213" stroke-width="1.5"/>
        <circle cx="8" cy="12.3" r="0.9" fill="#f07213"/>
      </svg>
      <span>555.214.7730</span>
    </li>
    <li class="contacts__item">
      <svg class="contacts__icon" viewBox="0 0 16 16" aria-hidden="true">
        <path d="M2 6 Q8 1 14 6 L12.5 7.5 L10.5 6 L10.5 5 Q8 4 5.5 5 L5.5 6 L3.5 7.5 Z" fill="#f07213"/>
        <rect x="3" y="8.5" width="10" height="6" rx="1" fill="#f07213"/>
      </svg>
      <span>+34 600 123 456</span>
    </li>
    <li class="contacts__item">
      <svg class="contacts__icon" viewBox="0 0 16 16" aria-hidden="true">
        <rect x="1" y="4" width="14" height="9" fill="#f07213"/>
        <path d="M1 4 L8 9.5 L15 4" fill="none" stroke="#1b1b1b" stroke-width="1.2"/>
      </svg>
      <span>info@coastlinepremierretreats.example</span>
    </li>
    <li class="contacts__item">
      <svg class="contacts__icon" viewBox="0 0 16 16" aria-hidden="true">
        <circle cx="8" cy="8" r="6.5" fill="none" stroke="#f07213" stroke-width="1.5"/>
        <ellipse cx="8" cy="8" rx="2.8" ry="6.5" fill="none" stroke="#f07213" stroke-width="1.2"/>
        <line x1="1.5" y1="8" x2="14.5" y2="8" stroke="#f07213" stroke-width="1.2"/>
      </svg>
      <span>www.<span class="contacts__domain">coastlinepremierretreats</span>.example</span>
    </li>
  </ul>
</section>

<section class="card card--back" aria-label="Business card back">
  <p class="back-mark">Coastline Premier<br>Retreats</p>
  <p class="tagline">Luxury Hotel &amp; Resort Email Marketing</p>
</section>

</body>
</html>
```